Drone service provider needs a brilliant web design

I need a responsive web design for a new drone service company. Pelham Drone Solutions provides turnkey solutions to capture, process, and deliver actionable aerial data to customers. The design should communicate a professional company that is safe, legal and insured. I included our logo design and business card designs for reference.
*content to be supplied after design selected

Target Market(s)

We serve telecommunications, construction, government, utility infrastructure, insurance and other industries.

Industry/Entity Type

Industrial

Number of Pages Required

5+ page

Colors

Designer to choose colors to be used in the design.

Requirements
Must have
• The design should highlight professional services to include Inspections, Mapping, Consulting and Training. The site should include aerial images and video to compliment the services offered. The landing page must include following sections in order: HOME, SERVICES, ABOUT, DEMO REEL, CLIENTS, CONTACT FORM, and social media buttons (Facebook, LinkedIn, Twitter, YouTube, Instagram). Contact: 615-382-9041 info@pelhamdronesolutions-example.com Smyrna, TN
• Sitemap:
• 6 pages: Home, Inspections, Mapping, Training, Consulting, About
• HOME (Landing Page)
• • Header with logo and tab links (Home, Services, About, Contact)
• • 'CAPTURE. PROCESS. DELIVER.' tagline and 'CONTACT US' button displayed within aerial image of drone over city or construction site
• • Services section with icons, text and read more link to page
• • About section with photo and text with three icons for SAFE. LEGAL. INSURED.
• • Demo reel
• • Clients logos shown scrolling horizontally
• • Contact form
• • Footer with logo, phone, email, social media buttons
• SERVICES (4 different pages)
• • Inspections
• • Mapping
• • Consulting
• • Training
• ABOUT page
• • Company
• • Partners
• • Certifications & Associations
• • Careers
• CONTACT linked to bottom of landing page
• Would you like to receive the newsletter? Yes or No Drop-down list
Nice to have
• Photos of KVR Marlin or Corvex inspecting infrastructure, buildings, construction sites, etc. A photo of one or two pilots in vest and helmet. Free stock photos preferred but would purchase the right photo that's more relevant.
• website references:
• https://www.quillrotor-example.com/
• https://www.brentfieldworks-example.com/services
• https://www.tomaro-example.com/
• http://gantrymetric-example.com/
• http://lumbrook-example.com/
• http://fennotics-example.com/
• https://www.grebe-example.io/
Should not have
• not an aerial photography or videography service business, no blog or newsletter

```html
<!DOCTYPE html>
<html lang="en">
<head>
<meta charset="utf-8">
<title>About Pelham – Pelham Drone Solutions</title>
<link rel="stylesheet" href="https://fonts.googleapis.com/css2?family=Roboto:wght@300;400;500;700&display=swap">
<style>
  :root {
    --orange: #f26a21;
    --ink: #2b2b2b;
    --body: #3a3a3a;
    --white: #ffffff;
    --footer: #5d5f60;
  }
  * { box-sizing: border-box; margin: 0; padding: 0; }
  html, body { width: 1200px; height: 2752px; overflow: hidden; }
  body { position: relative; background: var(--white); font-family: 'Roboto', Arial, sans-serif; color: var(--body); }
  .abs { position: absolute; }

  /* Hero */
  .hero { left: 0; top: 0; width: 1200px; height: 499px;
    background: linear-gradient(180deg,
      #f2f3f4 0%, #e6e8ea 14%,
      #c9ced4 22%, #dfe2e6 30%, #b5bbc2 40%, #d5d8dc 52%, #aeb3b8 62%,
      #4d5249 66%, #3e4339 74%, #5d605c 79%,
      #8f9194 82%, #a3a5a8 90%, #b1b3b6 100%); }
  .logo { font-weight: 700; font-size: 28px; letter-spacing: 1px; line-height: 1; }
  .hero-logo { left: 213px; top: 26px; color: var(--ink); }
  .menu { left: 943px; top: 32px; width: 36px; }
  .menu span { display: block; height: 2px; background: var(--ink); margin-bottom: 5px; }
  .menu span:nth-child(2) { width: 30px; margin-left: 6px; }
  .hero-title { left: 0; width: 1200px; top: 226px; text-align: center; color: var(--orange); font-size: 38px; font-weight: 400; letter-spacing: 2px; }
  .social { display: flex; gap: 6px; }
  .social span { width: 18px; height: 18px; border: 2px solid var(--ink); display: block; }
  .social span.active { border-color: var(--orange); }
  .hero-social { left: 211px; top: 456px; }

  /* Section titles */
  .section-title { text-align: center; font-size: 33px; font-weight: 400; letter-spacing: 2px; color: var(--ink); }
  .rule { height: 2px; background: var(--orange); }
  .plus { width: 24px; height: 24px; }
  .plus::before, .plus::after { content: ""; position: absolute; background: var(--orange); }
  .plus::before { left: 11px; top: 0; width: 2px; height: 24px; }
  .plus::after { left: 0; top: 11px; width: 24px; height: 2px; }

  /* Company */
  .company-title { left: 0; width: 1200px; top: 592px; }
  .company-text { left: 262px; width: 676px; top: 730px; text-align: center; font-size: 18.5px; line-height: 25.6px; color: var(--body); }
  .pillar { width: 172px; height: 172px; border-radius: 50%; background: var(--white);
    box-shadow: 0 6px 22px rgba(0,0,0,.22); display: flex; align-items: center; justify-content: center;
    color: var(--orange); font-size: 19px; font-weight: 500; letter-spacing: .5px; top: 945px; }

  /* Team */
  .team-photo { left: 600px; top: 1198px; width: 600px; height: 729px;
    background: linear-gradient(180deg, #9ebddf 0%, #b7cde5 14%, #5d6062 22%, #3f4244 40%, #545847 58%, #4b4e3c 78%, #5a5c48 100%); }
  .team-title { left: 486px; width: 257px; top: 1248px; }
  .portrait { left: 266px; top: 1376px; width: 209px; height: 287px;
    background: linear-gradient(180deg, #d9d9d9 0%, #cacaca 30%, #bdb6ae 48%, #434d3b 62%, #333d2d 100%); }
  .member-name { left: 226px; width: 289px; top: 1684px; text-align: center; color: var(--orange); font-size: 19px; letter-spacing: 1px; }
  .member-role { left: 226px; width: 289px; top: 1714px; text-align: center; font-size: 12px; color: var(--ink); }
  .member-bio { left: 278px; width: 185px; top: 1741px; text-align: center; font-size: 12px; line-height: 15.6px; color: var(--ink); }
  .dots { left: 332px; top: 1848px; display: flex; gap: 7px; }
  .dots span { width: 11px; height: 11px; border-radius: 50%; border: 1.5px solid var(--orange); display: block; }
  .dots span.on { background: var(--orange); }

  /* Standards */
  .standards { left: 0; top: 1927px; width: 1200px; height: 670px;
    background: linear-gradient(180deg,
      #c6c7ca 0%, #b9bbbe 22%, #a2a5a8 32%, #7e8184 40%, #9a9da0 48%,
      #c9cbcd 56%, #d6d7d9 64%, #b9aea6 70%, #c4bcb6 72%,
      #d3d4d6 76%, #d0d1d3 100%); }
  .standards-title { left: 0; width: 1200px; top: 2018px; }
  .standards-text { left: 268px; width: 664px; top: 2126px; text-align: center; color: var(--white); font-size: 18.5px; font-weight: 500; line-height: 25px; }
  .badge { width: 236px; text-align: center; top: 2271px; }
  .badge-icon { width: 118px; height: 118px; border-radius: 50%; background: rgba(255,255,255,.18);
    border: 1.5px solid rgba(255,255,255,.7); margin: 0 auto; display: flex; align-items: center; justify-content: center; }
  .badge-label { margin-top: 40px; color: var(--orange); font-size: 15px; font-weight: 700; letter-spacing: .5px; }
  .badge-text { margin-top: 12px; color: var(--white); font-size: 11.5px; line-height: 16px; padding: 0 40px; }

  /* Footer */
  .footer { left: 0; top: 2597px; width: 1200px; height: 155px; background: var(--footer); color: var(--white); }
  .footer-logo { left: 217px; top: 34px; color: var(--white); }
  .footer-info { top: 38px; font-size: 12.5px; letter-spacing: .3px; }
  .footer-social { left: 532px; top: 80px; }
  .footer-social span { border-color: var(--white); }
  .footer-social span.active { border-color: var(--orange); }
  .copyright { left: 0; width: 1200px; top: 128px; text-align: center; font-size: 10px; }
</style>
</head>
<body>

<header class="abs hero" role="img" aria-label="Photo of a white quadcopter drone resting on a road with snowy hills behind"></header>
<div class="abs logo hero-logo">PELHAM</div>
<div class="abs menu" aria-label="Menu"><span></span><span></span><span></span></div>
<h1 class="abs hero-title">About PELHAM</h1>
<nav class="abs social hero-social" aria-label="Social media">
  <span class="active"></span><span></span><span></span><span></span><span></span>
</nav>

<section>
  <h2 class="abs section-title company-title">The Company</h2>
  <div class="abs rule" style="left:473px;top:654px;width:252px"></div>
  <p class="abs company-text">Lorem ipsum dolor sit amet, consectetur adipisicing elit, sed do eiusmod tempor incididunt ut labore et dolore magna aliqua. Ut enim ad minim veniam, quis nostrud exercitation ullamco laboris nisi ut aliquip ex ea commodo consequat. Duis aute irure dolor in reprehenderit in voluptate velit esse cillum dolore eu fugiat nulla pariatur. Excepteur sint occaecat cupidatat non proident, sunt in culpa qui officia deserunt</p>
  <div class="abs plus" style="left:217px;top:928px"></div>
  <div class="abs pillar" style="left:266px">CAPTURE</div>
  <div class="abs pillar" style="left:514px">PROCESSING</div>
  <div class="abs pillar" style="left:762px">DELIVER</div>
  <div class="abs plus" style="left:953px;top:1118px"></div>
</section>

<section>
  <div class="abs team-photo" role="img" aria-label="Photo of a pilot in a flight helmet and oxygen mask against the sky"></div>
  <h2 class="abs section-title team-title">The Team</h2>
  <div class="abs rule" style="left:486px;top:1309px;width:257px"></div>
  <div class="abs plus" style="left:219px;top:1353px"></div>
  <div class="abs portrait" role="img" aria-label="Portrait photo of the company CEO"></div>
  <div class="abs member-name">JOHN DOE</div>
  <div class="abs member-role">CEO</div>
  <p class="abs member-bio">Lorem ipsum dolor sit amet, consectetur adipisicing elit, sed do eiusmod tempor incididunt ut labore et dolore magna aliqua. Ut enim ad</p>
  <div class="abs dots"><span class="on"></span><span></span><span></span><span></span></div>
  <div class="abs plus" style="left:533px;top:1873px"></div>
</section>

<section>
  <div class="abs standards" role="img" aria-label="Photo of a dark drone hovering over a blurred snowy landscape"></div>
  <h2 class="abs section-title standards-title">Pelham Standards</h2>
  <div class="abs rule" style="left:473px;top:2083px;width:254px"></div>
  <p class="abs standards-text">Lorem ipsum dolor sit amet, consectetur adipisicing elit, sed do eiusmod tempor incididunt ut labore et dolore magna aliqua. Ut enim ad minim veniam, quis nostrud exercitation ullamco laboris nisi ut aliquip</p>
  <div class="abs plus" style="left:214px;top:2219px"></div>

  <div class="abs badge" style="left:187px">
    <div class="badge-icon">
      <svg width="54" height="60" viewBox="0 0 54 60" fill="none" stroke="#fff" stroke-width="2"><path d="M27 3 L50 11 V28 C50 43 40 52 27 57 C14 52 4 43 4 28 V11 Z"/><path d="M16 30 L24 38 L38 22"/></svg>
    </div>
    <div class="badge-label">SAFE</div>
    <p class="badge-text">Lorem ipsum dolor sit amet, consectetur adipisicing elit, sed do eiusmod tempor incididunt ut labore et</p>
  </div>
  <div class="abs badge" style="left:383px">
    <div class="badge-icon">
      <svg width="60" height="56" viewBox="0 0 60 56" fill="none" stroke="#fff" stroke-width="2"><path d="M30 4 V48 M18 52 H42 M8 12 H52"/><path d="M8 12 L2 30 H14 Z M52 12 L46 30 H58 Z"/><path d="M2 30 C4 36 12 36 14 30 M46 30 C48 36 56 36 58 30"/></svg>
    </div>
    <div class="badge-label">LEGAL</div>
    <p class="badge-text">Lorem ipsum dolor sit amet, consectetur adipisicing elit, sed do eiusmod tempor incididunt ut labore et</p>
  </div>
  <div class="abs badge" style="left:579px">
    <div class="badge-icon">
      <svg width="60" height="60" viewBox="0 0 60 60" fill="none" stroke="#fff" stroke-width="2"><path d="M4 28 C6 14 17 6 30 6 C43 6 54 14 56 28 C52 24 46 24 43 28 C40 24 33 24 30 28 C27 24 20 24 17 28 C14 24 8 24 4 28 Z"/><path d="M30 28 V50 C30 56 22 56 22 50"/></svg>
    </div>
    <div class="badge-label">INSURED</div>
    <p class="badge-text">Lorem ipsum dolor sit amet, consectetur adipisicing elit, sed do eiusmod tempor incididunt ut labore et</p>
  </div>
  <div class="abs badge" style="left:777px">
    <div class="badge-icon">
      <svg width="60" height="60" viewBox="0 0 60 60" fill="none" stroke="#fff" stroke-width="2"><path d="M52 6 L22 40 L18 44 L14 42 L18 38 L48 4 Z"/><path d="M14 42 L6 54"/></svg>
    </div>
    <div class="badge-label">PILOTS</div>
    <p class="badge-text">Lorem ipsum dolor sit amet, consectetur adipisicing elit, sed do eiusmod tempor incididunt ut labore et</p>
  </div>
  <div class="abs plus" style="left:962px;top:2555px"></div>
</section>

<footer class="abs footer">
  <div class="abs logo footer-logo">PELHAM</div>
  <div class="abs footer-info" style="left:413px">Phone: +1 615 382 9041</div>
  <div class="abs footer-info" style="left:631px">Contact: contact@pelhamdrones-example.com</div>
  <nav class="abs social footer-social" aria-label="Social media">
    <span class="active"></span><span></span><span></span><span></span><span></span>
  </nav>
  <div class="abs copyright">PELHAM &copy; 2017 &nbsp; All Rights Reserves</div>
</footer>

</body>
</html>
```